Verodex business card

Business card for sustainable investment company called "Verodex". Verodex is an exchange platform selling carbon credits between buyers and sellers. Carbon Credits are an environmental commodity for reducing global carbon emissions.

the card should obviously have our logo and the theme should be sustainability/environment mixed with a trading platform.

Contact Information for Business Card

Logo, Name, Title, Phone, Email

Colors
0054AA
0677BA
7BADD7
CADEEF
E8F1F8
0094D4
00A9DD
6FCCEA
C7EBF8
E9F6FB
00AB8E
00BBA5
67D7C9
C6EFE9
E9F9F6
59FF00
82FF00
B8FF75
E3FFCB
F4FFEA

```html
<!DOCTYPE html>
<html lang="en">
<head>
<meta charset="UTF-8">
<title>Verodex Business Card</title>
<link rel="stylesheet" href="https://fonts.googleapis.com/css2?family=Montserrat:wght@600;700&family=Arimo:wght@400&display=swap">
<style>
  :root {
    --backdrop: #0d0e12;
    --card-top: #1a2440;
    --card-bottom: #1f2d4c;
    --ink-white: #f4f6fa;
    --ink-soft: #dfe5ef;
    --accent-blue: #1b63e0;
    --accent-cyan: #2fd4e6;
    --rule: #e6e9ef;
  }
  * { margin: 0; padding: 0; box-sizing: border-box; }
  html, body { width: 1200px; height: 963px; overflow: hidden; }
  body {
    background: var(--backdrop);
    position: relative;
    font-family: "Arimo", Arial, sans-serif;
  }
  .card {
    position: absolute;
    left: 290px;
    width: 620px;
    height: 354px;
    border-radius: 22px;
    background: linear-gradient(160deg, var(--card-top), var(--card-bottom));
    overflow: hidden;
    box-shadow: 0 18px 40px rgba(0,0,0,.55);
  }
  .card::after {
    content: "";
    position: absolute;
    inset: 0;
    border-radius: 22px;
    border-bottom: 3px solid transparent;
    border-right: 3px solid transparent;
    background: linear-gradient(90deg, var(--accent-cyan), var(--accent-blue)) border-box;
    -webkit-mask: linear-gradient(#000 0 0) padding-box, linear-gradient(#000 0 0);
    -webkit-mask-composite: xor;
    mask-composite: exclude;
    pointer-events: none;
  }
  .card--front { top: 70px; }
  .card--back { top: 520px; }

  .wordmark {
    display: flex;
    align-items: center;
    gap: 12px;
    font-family: "Montserrat", sans-serif;
    font-weight: 700;
    color: var(--ink-white);
    letter-spacing: .04em;
    text-transform: uppercase;
  }
  .wordmark__mark {
    background: var(--accent-cyan);
    border-radius: 3px;
  }
  .card--front .wordmark {
    position: absolute;
    left: 330px;
    top: 92px;
    font-size: 34px;
  }
  .card--front .wordmark__mark { width: 30px; height: 30px; }

  .person {
    position: absolute;
    left: 40px;
    top: 152px;
  }
  .person__name {
    font-family: "Montserrat", sans-serif;
    font-weight: 700;
    font-size: 17px;
    letter-spacing: .04em;
    text-transform: uppercase;
    background: linear-gradient(90deg, var(--accent-blue), var(--accent-cyan));
    -webkit-background-clip: text;
    background-clip: text;
    color: transparent;
  }
  .person__title {
    font-size: 13px;
    color: var(--ink-soft);
    margin-top: 2px;
  }
  .rule {
    position: absolute;
    left: 40px;
    top: 206px;
    width: 430px;
    height: 1.5px;
    background: var(--rule);
  }
  .contact {
    position: absolute;
    left: 40px;
    top: 218px;
    list-style: none;
  }
  .contact__item {
    display: flex;
    align-items: center;
    gap: 10px;
    font-size: 13px;
    color: var(--ink-white);
    line-height: 23px;
  }
  .contact__icon { width: 13px; height: 13px; flex: none; }
  .address {
    position: absolute;
    right: 150px;
    top: 222px;
    text-align: right;
    font-size: 13px;
    line-height: 19px;
    color: var(--ink-white);
  }

  .card--back .wordmark {
    position: absolute;
    left: 0; right: 0; top: 0; bottom: 0;
    justify-content: center;
    font-size: 44px;
  }
  .card--back .wordmark__mark { width: 38px; height: 38px; }
</style>
</head>
<body>
  <section class="card card--front" aria-label="Card front">
    <div class="wordmark"><span class="wordmark__mark"></span>Verodex</div>

    <div class="person">
      <p class="person__name">Marcus Hale</p>
      <p class="person__title">Manager</p>
    </div>

    <div class="rule"></div>

    <ul class="contact">
      <li class="contact__item">
        <svg class="contact__icon" viewBox="0 0 16 16"><path fill="#2f8cf0" d="M3.6 1.2l2.2 2.6-1.3 1.6c.9 2 2.4 3.5 4.3 4.4l1.6-1.3 2.6 2.2-1.2 2.3C7.2 12.8 3.1 8.8 1.3 2.4z"/></svg>
        555-208-7734
      </li>
      <li class="contact__item">
        <svg class="contact__icon" viewBox="0 0 16 16"><rect x="1.5" y="3.5" width="13" height="9" rx="1" fill="none" stroke="#2f8cf0" stroke-width="1.4"/><path d="M2 4.2l6 4.6 6-4.6" fill="none" stroke="#2f8cf0" stroke-width="1.4"/></svg>
        marcus@verodex.com
      </li>
      <li class="contact__item">
        <svg class="contact__icon" viewBox="0 0 16 16"><g fill="none" stroke="#2f8cf0" stroke-width="1.3"><circle cx="8" cy="8" r="6.3"/><ellipse cx="8" cy="8" rx="2.8" ry="6.3"/><path d="M1.7 8h12.6M2.6 5h10.8M2.6 11h10.8"/></g></svg>
        www.verodex.com
      </li>
    </ul>

    <p class="address">Your Address<br>City, State, Zip 0000</p>
  </section>

  <section class="card card--back" aria-label="Card back">
    <div class="wordmark"><span class="wordmark__mark"></span>Verodex</div>
  </section>
</body>
</html>
```